Cover for a book about building companies without hierarchy

We need to design the cover of our new book. In 2018 we have developed a new organizational design called "Velmorith" which mean equal, just in Latin. This organizational design is hierarchy-free, and it is formed by a radial network of self-organizing teams, where people can take decisions pertaining their job, be autonomous, and contribute to the well being of the larger organization. We published a book in 2018 (see the cover attached), titled: "Velmorith. The Open People-first Structural Model to Flourish in a Shifting Era", where we used the graphic representation of the Velmorith structure in the cover (see attached). The book is intended for top managers, entrepreneurs, businesses.
After 5 years from its launch, we implemented this design in a number of companies and we learned a lot about what works and the challenges. So we decided to publish another book that will be titled: "Velmorith. 5 pillars to shape a people-first office" where we present a revised model, we focus on the principles behind Velmorith and we tell the story of the implementation of Velmorith in Corvellan Italy.
The book cover design must include both front and back, using the template attached.
In the front we need to include: an image or illustration, the Names of the authors (Marisa Tolvengo and Lorenzo Brucani) and the Pelvaro logo.
In the back we shall include: an empty space for the ISDN code as in the template, a short description of the book, the pictures and short bios of the authors .
In the spine we shall include: the title and authors.
Here's the bios:
Marisa Tolvengo is a partner at Pelvaro, a global organizational development firm, a former executive in the corporate setting (including Brindle & Moss and Quibbit! Inc.) and Past President of WPN Global (Worldwide Practitioner Network). She is the author of the book “Inner Compass. The Road to Renewing Guidance” and a FORAx speaker.
Lorenzo Brucani is a partner at Pelvaro and a former manager in multinational settings. He is the co-author of the Calloway Management Journal articles “Why Your Inner Climate Shapes your Output”, “3 Ways to Lift a Gloomy Day”, “Preparing Your Inner Climate for a Holiday Break” and “An Easy Method to Ease Lasting Tension”.
Pictures of the authors attached.
The final versions of the book cover shall be:
- book cover for paperback in English (front and back)
- Book cover for paperback in Italian (front and back)
- Book cover for kindle (only front)

```html
<!DOCTYPE html>
<html lang="en">
<head>
<meta charset="utf-8">
<title>Velmorith – Book Cover Spread</title>
<link rel="stylesheet" href="https://fonts.googleapis.com/css2?family=Quicksand:wght@300;400;500;700&display=swap">
<style>
  :root {
    --stage: #282828;
    --paper: #f4f4f4;
    --navy: #1b1258;
    --plum: #3b1a60;
    --ink: #1c1c1c;
    --white: #ffffff;
    --brick: #8d5a44;
  }
  * { box-sizing: border-box; margin: 0; padding: 0; }
  html, body { width: 1200px; height: 1200px; overflow: hidden; }
  body {
    background: var(--stage);
    font-family: "Quicksand", sans-serif;
    color: var(--ink);
    position: relative;
  }
  .cover {
    position: absolute; left: 27px; top: 187px;
    width: 1146px; height: 826px;
    background: var(--paper);
    overflow: hidden;
  }
  .abs { position: absolute; }

  /* Back cover */
  .back-network {
    left: 184px; top: 0; width: 342px; height: 124px;
    background: radial-gradient(ellipse at 60% 40%, rgba(247,230,0,.55), rgba(227,25,94,.35) 45%, rgba(108,189,69,.25) 70%, rgba(244,244,244,0) 100%);
  }
  .back-title {
    left: 56px; top: 66px;
    font-weight: 300; font-size: 40px; letter-spacing: 4px;
    color: var(--plum); line-height: 1;
  }
  .back-subtitle {
    left: 56px; top: 109px; width: 340px;
    font-size: 15px; font-weight: 400; line-height: 19px; color: var(--ink);
  }
  .blurb {
    left: 60px; top: 158px; width: 441px;
    font-style: italic; font-size: 12.3px; line-height: 17.4px;
    text-align: center; color: var(--ink);
  }
  .author-photo { width: 88px; height: 113px; }
  .photo-one { left: 59px; top: 360px; background: linear-gradient(160deg, #e8e6e8, #d66a58 60%, #b0473e); }
  .photo-two { left: 60px; top: 509px; background: linear-gradient(160deg, var(--brick), #efefef 55%, #3c3f55); }
  .bio { width: 338px; font-size: 12.1px; line-height: 17.4px; color: var(--ink); }
  .bio b { font-weight: 700; }
  .bio-one { left: 163px; top: 363px; }
  .bio-two { left: 163px; top: 512px; }
  .brand-back {
    left: 65px; top: 722px;
    font-size: 26px; font-weight: 500; letter-spacing: 1px; color: var(--navy);
    display: flex; align-items: center; gap: 8px;
  }
  .brand-dot { width: 10px; height: 10px; border-radius: 50%; background: var(--navy); }
  .isbn-box { left: 346px; top: 685px; width: 178px; height: 107px; background: var(--white); }

  /* Spine */
  .spine { left: 535px; top: 0; width: 65px; height: 826px; }
  .spine-text {
    position: absolute; left: 50%; top: 52px;
    transform-origin: left top;
    transform: translateX(14px) rotate(90deg);
    white-space: nowrap; font-size: 25px; line-height: 28px; color: var(--ink);
    display: flex; align-items: center;
  }
  .spine-title { font-weight: 300; letter-spacing: 3px; color: var(--plum); width: 320px; }
  .spine-authors { font-weight: 400; }

  /* Front cover */
  .front-title {
    left: 640px; top: 58px; width: 490px;
    font-weight: 400; font-size: 64px; letter-spacing: 7px;
    color: var(--navy); line-height: 1; white-space: nowrap;
  }
  .front-network {
    left: 644px; top: 142px; width: 502px; height: 596px;
    background:
      radial-gradient(circle at 60% 50%, rgba(255,255,255,.9), rgba(255,255,255,0) 30%),
      radial-gradient(ellipse at 55% 50%, rgba(247,230,0,.55), rgba(227,25,94,.35) 50%, rgba(29,143,216,.2) 72%, rgba(244,244,244,0) 90%);
  }
  .core {
    left: 905px; top: 370px; width: 162px; height: 162px;
    border-radius: 50%; background: var(--navy);
    display: flex; align-items: center; justify-content: center; text-align: center;
    color: var(--white); font-weight: 700; font-size: 11.5px; line-height: 16.5px;
    padding: 0 26px;
  }
  .front-authors {
    left: 644px; top: 758px; width: 480px;
    font-size: 28px; font-weight: 400; white-space: nowrap; color: var(--ink);
  }
</style>
</head>
<body>
  <main class="cover">
    <section class="back">
      <div class="abs back-network" role="img" aria-label="Network illustration of coloured nodes linked by lines"></div>
      <h2 class="abs back-title">VELMORITH</h2>
      <p class="abs back-subtitle">5 Pillars to Shape a People-first Office</p>
      <p class="abs blurb">Is your organization failing to create the environment where real collaboration, innovation and speed are a natural habit and people are truly engaged? What if the real key to all this was a radical change in the way your organization is actually structured? The authors’ 15+ year experience in change initiatives, together with the outcomes of an extensive qualitative and quantitative research, led to the creation of Velmorith. Velmorith is a revolutionary organizational model based on a radial and peer- based structure of self-organized and coordinated teams that overcome the limits of the hierarchy and expands individual, team and organizational potential.</p>
      <div class="abs author-photo photo-one" role="img" aria-label="Portrait photo of Marisa Tolvengo"></div>
      <p class="abs bio bio-one"><b>Marisa Tolvengo</b> is a partner at Pelvaro, a global organizational development firm, a former executive in the corporate setting (including Brindle &amp; Moss and Quibbit! Inc.) and Past President of WPN Global (Worldwide Practitioner Network). She is the author of the book “Inner Compass. The Road to Renewing Guidance” and a FORAx speaker.</p>
      <div class="abs author-photo photo-two" role="img" aria-label="Portrait photo of Lorenzo Brucani"></div>
      <p class="abs bio bio-two"><b>Lorenzo Brucani</b> is a partner at Pelvaro and a former manager in multinational settings. He is the co-author of the Calloway Management Journal articles “Why Your Inner Climate Shapes your Output”, “3 Ways to Lift a Gloomy Day”, “Preparing Your Inner Climate for a Holiday Break” and “An Easy Method to Ease Lasting Tension”.</p>
      <div class="abs brand-back"><span class="brand-dot"></span>PELVARO</div>
      <div class="abs isbn-box"></div>
    </section>

    <section class="abs spine">
      <div class="spine-text">
        <span class="spine-title">VELMORITH</span>
        <span class="spine-authors">Marisa Tolvengo – Lorenzo Brucani</span>
      </div>
    </section>

    <section class="front">
      <h1 class="abs front-title">VELMORITH</h1>
      <div class="abs front-network" role="img" aria-label="Radial network illustration of coloured team nodes linked around a central hub"></div>
      <div class="abs core">5 Pillars to Shape a People-first Office</div>
      <p class="abs front-authors">Marisa Tolvengo – Lorenzo Brucani</p>
    </section>
  </main>
</body>
</html>
```